13 Varno - new website design project

Our company Varno Electrical is developing a new lead generation website focused on Electrical, LED Lighting and Solar Power. We need a high converting website.

Example of our current website is www.varnoelectrical-example.com.au You can take content from this website for this new design. Our colours are red, black and white. For our new website we would like to promote Varno, Spark Every Day. Please listen to the jingle.

The below link is the company jingle that we have developed.
http://www.tunecraftdemo.com.au/vrn-tc-v1/

The key for this brief is to generate leads for Electrical, LED Lighting (for commercial) and Solar Power & Storage.

Target Market(s)

Business owners in Melbourne Victoria

Number of Pages Required

4 page

Colors
ec1f27
ffffff

Requirements
Must have
• This page must be clean, be in line with company branding and a high converting lead website.

```html
<!DOCTYPE html>
<html lang="en">
<head>
<meta charset="utf-8">
<title>Varno Electrical</title>
<link href="https://fonts.googleapis.com/css2?family=Roboto:ital,wght@0,300;0,400;0,500;0,700;1,400&display=swap" rel="stylesheet">
<style>
:root{
  --red:#ec1f27;
  --red-soft:#ef5a5e;
  --red-light:#f58a8a;
  --red-pale:#fbd0d1;
  --ink:#1d1d1f;
  --text:#555a60;
  --muted:#8a8f95;
  --white:#ffffff;
  --panel:#f3f4f6;
  --bar:#eeeff1;
}
*{box-sizing:border-box;margin:0;padding:0}
html,body{width:672px;height:1200px;overflow:hidden;background:var(--white)}
body{font-family:'Roboto',Arial,sans-serif;color:var(--text);position:relative}
.abs{position:absolute}
h2{font-size:13px;font-weight:700;color:var(--ink);line-height:1.2}
h2 em{font-style:normal;color:var(--red)}
.rule{border-top:1px dashed var(--red-light)}

/* header + hero */
.hero{left:0;top:0;width:672px;height:310px;
  background:
    linear-gradient(200deg,rgba(255,255,255,0) 0%,rgba(255,255,255,0) 55%,rgba(20,30,80,.35) 100%),
    linear-gradient(162deg,#5f93d6 0%,#9cc2ea 28%,#c9dbee 40%,#5d6fa8 52%,#34418a 68%,#2a3574 100%)}
.hero-band{left:0;top:0;width:672px;height:37px;background:linear-gradient(90deg,var(--red-soft),var(--red-light))}
.brand{left:26px;top:0;width:165px;height:55px;background:var(--white);border-radius:0 0 6px 6px;display:flex;align-items:center;justify-content:center;gap:8px}
.brand-dot{width:14px;height:14px;border-radius:50%;background:var(--red)}
.brand-name{font-weight:700;font-size:20px;color:var(--ink);letter-spacing:.5px}
.nav{left:346px;top:13px;display:flex;gap:21px}
.nav a{color:var(--white);font-size:9.6px;font-weight:500;text-decoration:none;text-transform:uppercase}
.hero-badge{left:290px;top:94px;width:132px;height:132px;border-radius:50%;background:rgba(110,122,150,.55);display:flex;flex-direction:column;align-items:center;justify-content:center;color:var(--white);text-transform:uppercase;line-height:1.05}
.hero-badge .l1{font-size:17px;font-weight:300;letter-spacing:1px}
.hero-badge .l2{font-size:24px;font-weight:700}
.hero-badge .l3{font-size:16px;font-weight:300;letter-spacing:1px}

/* info bar */
.infobar{left:0;top:310px;width:672px;height:19px;background:var(--bar);display:flex;align-items:center;padding:0 28px;font-size:7.2px;color:var(--muted)}
.infobar .item{display:flex;align-items:center;gap:4px;margin-right:16px}
.infobar .right{margin-left:auto;display:flex;align-items:center;gap:14px}
.book{background:var(--red);color:var(--white);font-weight:700;font-size:7px;padding:2px 5px;border-radius:3px}
.soc{width:7px;height:7px;background:#9a9ea4;border-radius:1px}

/* welcome */
.welcome{left:29px;top:336px;width:299px;text-align:center}
.welcome .rule{margin:5px 0 7px}
.welcome p{font-size:7.2px;line-height:1.55;margin-bottom:8px}
.why{font-size:9.6px;margin-top:1px}
.features{position:relative;height:44px;margin-top:8px}
.features::before{content:"";position:absolute;left:30px;right:18px;top:13px;border-top:1px solid var(--red-light)}
.feature{position:absolute;top:0;width:80px;margin-left:-40px;display:flex;flex-direction:column;align-items:center;font-size:5.8px;font-weight:700;color:var(--ink);white-space:nowrap}
.feature .ic{width:27px;height:27px;border-radius:50%;background:var(--red);display:flex;align-items:center;justify-content:center;margin-bottom:7px;box-shadow:0 0 0 2px var(--red-pale)}
.feature.active{color:var(--red)}
.video{left:364px;top:335px;width:294px;height:165px;
  background:linear-gradient(170deg,#b8d0e6 0%,#8fb0cf 20%,#2e3b6c 38%,#3c4463 55%,#7a6c66 75%,#6a5f5c 100%)}
.play{left:490px;top:404px;width:45px;height:32px;border-radius:7px;background:var(--red);display:flex;align-items:center;justify-content:center}

/* services */
.services{left:0;top:508px;width:672px;height:176px;background:var(--panel)}
.tabs{position:absolute;left:190px;top:7px;display:flex;gap:6px}
.tab{font-size:10.5px;font-weight:500;color:var(--ink);padding:6px 10px;border:1px solid transparent}
.tab.on{color:var(--red);border-color:var(--red);border-radius:3px;background:var(--white)}
.services .rule{position:absolute;left:29px;right:29px;top:41px}
.svc{position:absolute;top:54px;width:104px;margin-left:-52px;text-align:center;font-size:11px;font-weight:500;color:var(--ink);line-height:1.2}
.svc .ph{width:79px;height:79px;border-radius:50%;margin:0 auto 7px}

/* lead form */
.leadform{left:0;top:684px;width:672px;height:50px;background:linear-gradient(90deg,#e84a4e,var(--red-light))}
.leadform .arrow{position:absolute;left:28px;top:17px}
.leadform .label{position:absolute;left:63px;top:14px;color:var(--white);font-size:7px;font-weight:500;line-height:1.6;width:60px}
.field{position:absolute;top:16px;width:142px;height:18px;background:var(--white);border-radius:3px;font-size:7px;color:var(--muted);display:flex;align-items:center;padding-left:8px}
.submit{position:absolute;left:590px;top:16px;width:54px;height:18px;background:var(--white);border-radius:3px;font-size:7px;font-weight:700;color:var(--ink);display:flex;align-items:center;justify-content:center}

/* projects */
.projects-head{left:29px;top:743px;width:614px;text-align:center}
.projects-head .rule{margin-top:6px}
.projects{left:0;top:782px;width:672px;height:104px;display:flex}
.projects div{flex:1}

/* testimonials */
.people{left:0;top:902px;width:672px;height:228px;background:var(--panel)}
.people-head{position:absolute;left:29px;right:29px;top:10px;text-align:center}
.people-head .rule{margin-top:6px}
.divider-v{position:absolute;left:336px;top:56px;height:126px;border-left:1px dashed var(--red-light)}
.divider-h{position:absolute;left:29px;right:29px;top:119px;border-top:1px dashed var(--red-light)}
.quote{position:absolute;width:230px}
.quote p{font-size:7.2px;font-style:italic;line-height:1.55;color:var(--text)}
.quote .who{font-style:normal;font-size:7.6px;color:var(--ink);margin-top:4px}
.quote.l{left:28px;text-align:right}
.quote.r{left:414px;width:230px}
.avatar{position:absolute;width:43px;height:43px;border-radius:50%;background:radial-gradient(circle at 50% 40%,#e2d6cc 0%,#b8aaa0 60%,#6e6460 100%)}
.skyline{position:absolute;left:0;bottom:0;width:672px;height:40px;background:linear-gradient(180deg,rgba(236,31,39,0) 0%,rgba(236,31,39,.25) 45%,rgba(236,31,39,.85) 90%,var(--red) 100%)}

/* footer */
.footer{left:0;top:1130px;width:672px;height:70px;background:var(--white);border-top:2px solid var(--red)}
.foot-top{position:absolute;left:34px;top:24px;display:flex;gap:16px;font-size:7.8px;font-weight:500;color:var(--ink);align-items:center}
.foot-rule{position:absolute;left:34px;right:29px;top:40px;border-top:1px dashed #d0d2d6}
.foot-links{position:absolute;left:34px;top:47px;display:flex;gap:11px;font-size:6.8px;color:var(--ink)}
.foot-right{position:absolute;right:29px;top:47px;display:flex;gap:10px;font-size:6.8px;color:var(--ink);align-items:center}
.foot-brand{position:absolute;right:29px;top:14px;display:flex;align-items:center;gap:5px;font-weight:700;font-size:13px;color:var(--ink)}
.foot-brand .brand-dot{width:11px;height:11px}
.sq{width:9px;height:9px;background:var(--red);border-radius:1px}
.bottom-bar{left:0;bottom:0;width:672px;height:3px;background:var(--red)}
</style>
</head>
<body>

<section class="abs hero" role="img" aria-label="Photo of an electrician installing solar panels on a house roof under blue sky"></section>
<div class="abs hero-band"></div>
<div class="abs brand"><span class="brand-dot"></span><span class="brand-name">Varno</span></div>
<nav class="abs nav"><a href="#">Home</a><a href="#">Our Company</a><a href="#">Services</a><a href="#">Works</a><a href="#">Contact Us</a></nav>
<div class="abs hero-badge"><span class="l1">Do you</span><span class="l2">Need</span><span class="l3">a</span><span class="l3">Electrician</span></div>

<div class="abs infobar">
  <span class="item"><svg width="7" height="7" viewBox="0 0 10 10"><path d="M2 1l2 2-1 1.5a6 6 0 003 3L7.5 6.5l2 2-1.5 1.5C4 10 0 6 0 2.5z" fill="#9a9ea4"/></svg>+1 13 47 20</span>
  <span class="item"><svg width="8" height="6" viewBox="0 0 10 7"><rect width="10" height="7" fill="#9a9ea4"/><path d="M0 0l5 4 5-4" stroke="#eee" fill="none"/></svg>service@varnoelectrical-example.com.au</span>
  <div class="right"><span class="book">Book Online</span><span class="soc"></span><span class="soc"></span><span class="soc"></span>
    <svg width="8" height="8" viewBox="0 0 10 10"><circle cx="4" cy="4" r="3" stroke="#9a9ea4" stroke-width="1.5" fill="none"/><path d="M6.5 6.5L9.5 9.5" stroke="#9a9ea4" stroke-width="1.5"/></svg></div>
</div>

<section class="abs welcome">
  <h2>Welcome to <em>Varno Electrical</em></h2>
  <div class="rule"></div>
  <p>Varno Electrical was formed to be an expert Electricity Contracting Company providing services to all Residential and Commercial Customers.</p>
  <p>With over 10 years of experience, Varno Electrical has developed a highly-experienced team of professionals that ensure all our customer expectations are met.</p>
  <h2 class="why">Why <em>Choose Us</em></h2>
  <div class="features">
    <div class="feature" style="left:29px"><span class="ic"><svg width="12" height="12" viewBox="0 0 12 12"><circle cx="6" cy="5" r="3.5" fill="none" stroke="#fff" stroke-width="1.3"/><rect x="4.5" y="9" width="3" height="2" fill="#fff"/></svg></span>Professional Service</div>
    <div class="feature" style="left:113px"><span class="ic"><svg width="12" height="12" viewBox="0 0 12 12"><path d="M2 6.5l2.5 2.5L10 3" stroke="#fff" stroke-width="2" fill="none"/></svg></span>5 Year Guarantee</div>
    <div class="feature active" style="left:199px"><span class="ic"><svg width="12" height="12" viewBox="0 0 12 12"><path d="M6 1C2 4 2 8 6 11c4-3 4-7 0-10z" fill="#fff"/></svg></span>Environmentally friendly</div>
    <div class="feature" style="left:282px"><span class="ic"><svg width="12" height="12" viewBox="0 0 12 12"><rect x="1.5" y="3" width="9" height="7" rx="1" fill="none" stroke="#fff" stroke-width="1.3"/><rect x="7" y="5.5" width="3.5" height="2" fill="#fff"/></svg></span>Value for Money</div>
  </div>
</section>
<div class="abs video" role="img" aria-label="Video still of a technician standing beside rooftop solar panels"></div>
<div class="abs play"><svg width="14" height="14" viewBox="0 0 10 10"><path d="M2 1l7 4-7 4z" fill="#fff"/></svg></div>

<section class="abs services">
  <div class="tabs"><span class="tab on">Residential</span><span class="tab">Commercial</span><span class="tab">Property Management</span></div>
  <div class="rule"></div>
  <div class="svc" style="left:74px"><div class="ph" role="img" aria-label="Photo of electrician testing a power outlet" style="background:linear-gradient(135deg,#2c3c78 0%,#4a5a94 50%,#b8b4b0 100%)"></div>Electrical Faults<br>&amp; Rewiring</div>
  <div class="svc" style="left:177px"><div class="ph" role="img" aria-label="Photo of an alarm keypad" style="background:linear-gradient(135deg,#e6e7e9 0%,#c4c6ca 55%,#8e9196 100%)"></div>Alarms Security<br>Systems</div>
  <div class="svc" style="left:280px"><div class="ph" role="img" aria-label="Photo of a hand on a light switch" style="background:linear-gradient(135deg,#8fb5a6 0%,#6f9d8d 50%,#d8c2b0 100%)"></div>Light Fittings &amp;<br>Switches</div>
  <div class="svc" style="left:383px"><div class="ph" role="img" aria-label="Photo of a switchboard installation" style="background:linear-gradient(135deg,#8a8884 0%,#4e4a46 50%,#d2702c 100%)"></div>Installations,<br>Service Repairs</div>
  <div class="svc" style="left:486px"><div class="ph" role="img" aria-label="Photo of a suburban home" style="background:linear-gradient(180deg,#a8c4e0 0%,#c9b8a6 45%,#8a7a6a 70%,#5e8a3e 100%)"></div>Home<br>Security</div>
  <div class="svc" style="left:589px"><div class="ph" role="img" aria-label="Photo of a multimeter testing a commercial panel" style="background:linear-gradient(135deg,#b03a40 0%,#5a2226 50%,#3a3a3a 100%)"></div>Commercial<br>Maintenance</div>
</section>

<section class="abs leadform">
  <svg class="arrow" width="20" height="16" viewBox="0 0 20 16"><path d="M2 15C2 8 6 5 13 5V1l6 6-6 6V9C8 9 4 11 2 15z" fill="#fff"/></svg>
  <span class="label">Book Free Site Audit</span>
  <span class="field" style="left:134px">Full Name *</span>
  <span class="field" style="left:286px">Phone Number *</span>
  <span class="field" style="left:438px">Your Email *</span>
  <span class="submit">SUBMIT</span>
</section>

<section class="abs projects-head"><h2>Latest <em>Projects</em></h2><div class="rule"></div></section>
<section class="abs projects">
  <div role="img" aria-label="Photo of a company van beside a house" style="background:linear-gradient(180deg,#9cc0e4 0%,#6c7282 45%,#e8e8ea 70%,#5a5e62 100%)"></div>
  <div role="img" aria-label="Photo of rooftop solar panels" style="background:linear-gradient(170deg,#8ab4e0 0%,#5a5c66 30%,#3848a0 55%,#26307a 100%)"></div>
  <div role="img" aria-label="Photo of an electrician at a meter box" style="background:linear-gradient(90deg,#5e7a4a 0%,#d8d8d4 35%,#2c2c2e 60%,#9a9a96 100%)"></div>
  <div role="img" aria-label="Photo of a lit warehouse interior" style="background:linear-gradient(180deg,#6a6a64 0%,#b8a878 35%,#d4c890 55%,#8a8a86 100%)"></div>
  <div role="img" aria-label="Photo of warehouse shelving" style="background:linear-gradient(90deg,#8d8376 0%,#c4b6a0 40%,#6a625a 70%,#a89a86 100%)"></div>
</section>

<section class="abs people">
  <div class="people-head"><h2>What <em>People Say</em></h2><div class="rule"></div></div>
  <div class="divider-v"></div>
  <div class="divider-h"></div>

  <div class="quote l" style="top:58px"><p>Duis aute irure dolor in reprehenderit in voluptate velit esse cillum dolore eu fugiat nulla pariatur. Excepteur sint occaecat cupidatat non proident, sunt in culpa qui officia deserunt mollit.</p><p class="who">Owen Harlow, Operations Manager</p></div>
  <div class="avatar" style="left:275px;top:58px" role="img" aria-label="Customer portrait"></div>

  <div class="avatar" style="left:354px;top:58px" role="img" aria-label="Customer portrait"></div>
  <div class="quote r" style="top:58px"><p>Provident, similique sunt in culpa qui officia deserunt mollitia animi, id est laborum et dolorum fuga. Et harum quidem rerum facilis est et expedita distinctio. Nam libero tempore, cum soluta nobis.</p><p class="who">Nina Castell, Creative Designer</p></div>

  <div class="quote l" style="top:136px"><p>Luis aute irure dolor in reprehenderit in piluptate velit esse cillum dolore eu fugiat nulla pariatur. Excepteur sint occaecat cupidatat non proident, sunt in culpa qui officia deserunt mollit.</p><p class="who">Ruth Pemberly, Manager</p></div>
  <div class="avatar" style="left:275px;top:136px" role="img" aria-label="Customer portrait"></div>

  <div class="avatar" style="left:354px;top:136px" role="img" aria-label="Customer portrait"></div>
  <div class="quote r" style="top:136px"><p>At vero eos et accusamus et iusto odio dignissimos ducimus qui blanditiis praesentium voluptatum deleniti atque corrupti quos dolores et quas molestias excepturi sint occaecati.</p><p class="who">Sam Quarrie, Developer</p></div>

  <div class="skyline" role="img" aria-label="Red city skyline and airport silhouette illustration"></div>
</section>

<footer class="abs footer">
  <div class="foot-top"><svg width="8" height="8" viewBox="0 0 10 10"><circle cx="4" cy="4" r="3" stroke="#1d1d1f" stroke-width="1.5" fill="none"/><path d="M6.5 6.5L9.5 9.5" stroke="#1d1d1f" stroke-width="1.5"/></svg><span>Help &amp; Contact</span><span>Services</span><span>Our Work</span></div>
  <div class="foot-brand"><span class="brand-dot"></span>Varno</div>
  <div class="foot-rule"></div>
  <div class="foot-links"><span>About</span><span>Blog</span><span>Jobs</span><span>Public Policy</span><span>Sitemap</span><span>Partners</span></div>
  <div class="foot-right"><span>© 2012–2017</span><span>Privacy</span><span>Legal</span><span class="sq"></span><span class="sq"></span><span class="sq"></span></div>
</footer>
<div class="abs bottom-bar"></div>

</body>
</html>
```